Business Card Design Project : Ridgeline Press

In preparation for market launch, Tamarind's Ridgeline Press require the development of a business card. Ridgeline Press is a Community online publishing web portal. We provide the the city of Whistler located in B.C. (Canada) business directories, News, Classified ads, News, Events and blogs etc.

The main focus of the brand is to help local businesses to corporate with their online advertisement and marketing. Meeting our clients face to face is a must (B2B).

Target Market(s)

The target market is B2B customers. Business Owners to Marketing, advertising Managers

Industry/Entity Type

Business

Requirements
Must have
• - The business card will be two sided.
the BACK side will have our logo which consist of (icon, url,slogan) submited. The logo will be middle and centred.

The FRONT side should have company details:

Company Legal Name: TAMARIND RIDGELINE MEDIA

Owen Farsk
Director of Sales & Marketing

www.tamarindridgeline.biz
owen@tamarindridgeline.biz

Phone: 604 317 8842
#2714 - 582 E. Halvern St.
Vancouver, B.C. V7K2R4 Canada
Nice to have
• - For the "FRONT" side of our business card. You can separate or re-arrange with our logo components (icon, logo,slogan). It does not have to be together.

Also our company legal name is rather long so arrange or organize the name in a way to make it shorter. Your experience and creativity will have to come in play.
Should not have
• should not have other colors beside logo color and black text (2 colors). Also nothing Three dimensional

```html
<!DOCTYPE html>
<html lang="en">
<head>
<meta charset="utf-8">
<title>Ridgeline Press – Business Card</title>
<link rel="stylesheet" href="https://fonts.googleapis.com/css2?family=Arimo:wght@700&family=Source+Sans+3:wght@400;600;700&display=swap">
<style>
  :root {
    --brand-blue: #0a7cc4;
    --ink: #3a3a3a;
    --ink-soft: #555555;
    --band: #2a2a2a;
    --paper: #ffffff;
    --backdrop: #2e2e2e;
  }
  * { margin: 0; padding: 0; box-sizing: border-box; }
  html, body {
    width: 1200px; height: 798px; overflow: hidden;
    background: var(--backdrop);
  }
  .stage { position: relative; width: 1200px; height: 798px; }

  .card {
    position: absolute; width: 515px; height: 294px;
    background: var(--paper); overflow: hidden;
  }

  /* Back side: logo block */
  .card--back { left: 216px; top: 104px; }
  .brand-mark {
    position: absolute; left: 0; right: 0; top: 62px;
    display: flex; flex-direction: column; align-items: center;
  }
  .brand-mark__dot {
    width: 46px; height: 46px; border-radius: 50%;
    background: var(--brand-blue); margin-bottom: 28px;
  }
  .brand-mark__url {
    font-family: "Source Sans 3", sans-serif; font-weight: 700;
    font-size: 23px; color: var(--ink); line-height: 1; letter-spacing: -0.2px;
  }
  .brand-mark__slogan {
    font-family: "Source Sans 3", sans-serif; font-weight: 400;
    font-size: 17px; color: var(--brand-blue); line-height: 1; margin-top: 4px;
  }

  /* Front side: details */
  .card--front { left: 473px; top: 416px; }
  .identity-panel {
    position: absolute; left: 0; top: 0; width: 258px; height: 100%;
    background: var(--brand-blue);
  }
  .identity-panel__name {
    position: absolute; left: 0; right: 0; top: 100px;
    text-align: center; color: var(--paper);
    font-family: "Arimo", sans-serif; font-weight: 700;
    font-size: 25px; line-height: 29px; letter-spacing: 0.3px;
  }
  .identity-panel__band {
    position: absolute; left: 0; right: 0; top: 161px; height: 20px;
    background: var(--band); color: var(--paper);
    font-family: "Arimo", sans-serif; font-weight: 700; font-size: 12px;
    letter-spacing: 14px; text-indent: 14px;
    display: flex; align-items: center; justify-content: center;
  }

  .contact {
    position: absolute; left: 293px; top: 85px;
    font-family: "Source Sans 3", sans-serif; color: var(--ink-soft);
    font-size: 11.5px; line-height: 15px;
  }
  .contact__name { font-weight: 700; font-size: 15px; line-height: 17px; color: var(--ink); }
  .contact__title { font-weight: 600; font-size: 11.5px; color: var(--ink); margin-bottom: 10px; }
  .contact__block { margin-bottom: 6px; }
</style>
</head>
<body>
<main class="stage">
  <section class="card card--back" aria-label="Card back">
    <div class="brand-mark">
      <span class="brand-mark__dot" aria-hidden="true"></span>
      <p class="brand-mark__url">www.tamarindridgeline.biz</p>
      <p class="brand-mark__slogan">Your information gateway</p>
    </div>
  </section>

  <section class="card card--front" aria-label="Card front">
    <div class="identity-panel">
      <p class="identity-panel__name">TAMARIND<br>RIDGELINE</p>
      <p class="identity-panel__band">MEDIA</p>
    </div>
    <div class="contact">
      <p class="contact__name">Owen Farsk</p>
      <p class="contact__title">Director of Sales &amp; Marketing</p>
      <p class="contact__block">#2714 - 582 E. Halvern<br>St.Vancouver, B.C. V7K2R4 Canada</p>
      <p class="contact__block">Phone: 604 317 8842<br>Email: owen@tamarindridgeline.biz</p>
      <p>www.tamarindridgeline.biz</p>
    </div>
  </section>
</main>
</body>
</html>
```